Civora88 - a Political Plebescite app.

There is a current app in the App Store (worldwide) and Play Store (worldwide) called yourStance (with an owl logo). The UX needs to be redesigned to make it more visually pleasing.

The requirement is to build a UX that is suitable for both iOS and Android - i.e. consistent look for both platforms. The design is to span the variety of sizes available from smart devices - phones and tablets. The layout as it stands is portrait only, and a secondary design to encompass landscape is wanted.

You would need to download the app to get a feel for all the functionality - there are 3 visible forms (currently) and a hidden form, that will be used in the near future - this hidden form will look similar to the main (first) form.

To get full functionality you need to do the following:
Go to the Options page
Toggle the top slide
Click on UNREGISTERED
Select a state/territory

I know this is a bit non-intuitive - in the "real" product these steps are automated - but for this release the user gets to choose.

Once this is done - the other button(s) appear in the top left of the screen - and data is available to be displayed.

The current forms are included in this brief. The Options screen will ultimately not be showing all the current data, only the lower slider (or other indicator) and the associated version and copyright notices. The hidden screen is much like the main screen - showing the name of the bill and information pertaining to that bill - there needs to be a button (or action site) to toggle between the main and this hidden screen.

Target Market(s)

All eligable voters (currently in Australia)

Industry/Entity Type

Political

Requirements
Should not have
• Do not present to me my own/existing design with the only change being colours and label layout.

```html
<!DOCTYPE html>
<html lang="en">
<head>
<meta charset="utf-8">
<title>Civora88 – Bill</title>
<link href="https://fonts.googleapis.com/css2?family=Roboto:wght@300;400&display=swap" rel="stylesheet">
<style>
  :root {
    --header-grey: #d1d4d7;
    --status-text: #ffffff;
    --title-navy: #3b4a6e;
    --body-text: #5a5a5a;
    --no-red: #f50f0f;
    --no-label: #e01010;
    --party-navy: #1f2d4a;
    --yes-green: #0a870a;
    --state-green: #3f8a6c;
    --state-red: #a3291f;
    --nav-bar: #45527a;
    --nav-divider: #6b779a;
    --page-top: #f4f4f5;
    --page-bottom: #e4e5e7;
  }
  * { box-sizing: border-box; margin: 0; padding: 0; }
  html, body { width: 674px; height: 1200px; overflow: hidden; }
  body {
    font-family: "Roboto", sans-serif;
    position: relative;
    background: linear-gradient(180deg, var(--page-top) 0%, #ffffff 40%, var(--page-bottom) 100%);
  }
  .top-band {
    position: absolute; left: 0; top: 0; width: 674px; height: 174px;
    background: var(--header-grey);
  }
  .status-bar {
    position: absolute; left: 0; top: 0; width: 674px; height: 44px;
    color: var(--status-text); font-size: 24px; font-weight: 300;
  }
  .status-bar .carrier { position: absolute; left: 14px; top: 6px; display: flex; align-items: center; gap: 6px; }
  .status-bar .time { position: absolute; left: 0; right: 0; top: 6px; text-align: center; }
  .status-bar .battery { position: absolute; right: 12px; top: 6px; display: flex; align-items: center; gap: 8px; }
  .region-switch { position: absolute; top: 74px; left: 236px; display: flex; align-items: center; }
  .region { display: block; }
  .region.active {
    width: 52px; height: 52px; border-radius: 50%; background: #fff;
    display: flex; align-items: center; justify-content: center;
  }
  .bill-title {
    position: absolute; left: 30px; top: 214px;
    font-size: 27px; font-weight: 400; color: var(--title-navy);
  }
  .no-document { position: absolute; left: 604px; top: 208px; }
  .bill-summary {
    position: absolute; left: 30px; top: 280px; width: 612px;
    font-size: 17.6px; line-height: 29.4px; color: var(--body-text);
    hyphens: auto; -webkit-hyphens: auto;
  }
  .vote-options { position: absolute; top: 875px; left: 0; width: 674px; }
  .vote {
    position: absolute; width: 90px; text-align: center; top: 0;
    font-size: 18px;
  }
  .vote .button {
    width: 70px; height: 70px; border-radius: 50%; margin: 0 auto;
    display: flex; align-items: center; justify-content: center;
  }
  .vote .label { display: block; margin-top: 12px; }
  .vote.no { left: 175px; color: var(--no-label); }
  .vote.no .button { background: var(--no-red); }
  .vote.party { left: 292px; color: var(--party-navy); }
  .vote.party .button { background: var(--party-navy); }
  .vote.yes { left: 409px; color: var(--yes-green); }
  .vote.yes .button { background: var(--yes-green); }
  .chamber {
    position: absolute; left: 30px; top: 1061px; display: flex; align-items: center;
    font-size: 18px; color: #333; font-weight: 300;
  }
  .chamber .dot { width: 17px; height: 17px; border-radius: 50%; background: var(--yes-green); margin-right: 22px; }
  .bill-counter { position: absolute; right: 18px; top: 1069px; font-size: 21px; color: #222; font-weight: 300; }
  .nav-bar {
    position: absolute; left: 0; top: 1115px; width: 674px; height: 85px;
    background: var(--nav-bar); display: flex;
  }
  .nav-item { flex: 1; display: flex; align-items: center; justify-content: center; }
  .nav-item + .nav-item { border-left: 1px solid var(--nav-divider); }
</style>
</head>
<body>
  <div class="top-band"></div>

  <div class="status-bar">
    <div class="carrier">
      <svg width="78" height="14" viewBox="0 0 78 14" aria-hidden="true">
        <circle cx="7" cy="7" r="6" fill="#fff"/><circle cx="22" cy="7" r="6" fill="#fff"/><circle cx="37" cy="7" r="6" fill="#fff"/>
        <circle cx="52" cy="7" r="5.3" fill="none" stroke="#fff" stroke-width="1.4"/><circle cx="67" cy="7" r="5.3" fill="none" stroke="#fff" stroke-width="1.4"/>
      </svg>
      <span>KESTREL</span>
      <svg width="24" height="18" viewBox="0 0 24 18" aria-hidden="true">
        <path d="M12 17 L8 12.5 A6 6 0 0 1 16 12.5 Z" fill="#fff"/>
        <path d="M4.5 9 A11 11 0 0 1 19.5 9" fill="none" stroke="#fff" stroke-width="2.4"/>
        <path d="M1 5 A16 16 0 0 1 23 5" fill="none" stroke="#fff" stroke-width="2.4"/>
      </svg>
    </div>
    <div class="time">4:21 PM</div>
    <div class="battery">
      <svg width="14" height="24" viewBox="0 0 14 24" aria-hidden="true"><path d="M2 7 L12 17 L7 22 V2 L12 7 L2 17" fill="none" stroke="#fff" stroke-width="1.6"/></svg>
      <span>100%</span>
      <svg width="52" height="22" viewBox="0 0 52 22" aria-hidden="true">
        <rect x="1" y="1" width="46" height="20" rx="3" fill="none" stroke="#fff" stroke-width="1.5"/>
        <rect x="3.5" y="3.5" width="41" height="15" rx="1.5" fill="#fff"/>
        <rect x="48.5" y="7" width="3" height="8" rx="1" fill="#fff"/>
      </svg>
    </div>
  </div>

  <nav class="region-switch">
    <span class="region active"><span role="img" aria-label="New South Wales state map, green" style="display:block;width:38px;height:28px;background:var(--state-green);border-radius:3px 8px 4px 10px;"></span></span>
    <span class="region" role="img" aria-label="New South Wales state map, red" style="width:38px;height:30px;background:var(--state-red);border-radius:3px 8px 4px 12px;margin-left:12px;"></span>
    <span class="region" role="img" aria-label="Australia map, green" style="width:40px;height:36px;background:var(--state-green);border-radius:40% 45% 50% 40%;margin-left:14px;"></span>
    <span class="region" role="img" aria-label="Australia map, red" style="width:40px;height:36px;background:var(--state-red);border-radius:40% 45% 50% 40%;margin-left:14px;"></span>
  </nav>

  <h1 class="bill-title">Crimes Amendment (Harper’s Law) Bill 2015</h1>
  <svg class="no-document" width="44" height="44" viewBox="0 0 44 44" aria-label="No bill document">
    <rect x="13" y="10" width="18" height="24" rx="2" fill="none" stroke="#555" stroke-width="1.6"/>
    <line x1="17" y1="17" x2="27" y2="17" stroke="#555" stroke-width="1.4"/>
    <line x1="17" y1="22" x2="27" y2="22" stroke="#555" stroke-width="1.4"/>
    <line x1="17" y1="27" x2="24" y2="27" stroke="#555" stroke-width="1.4"/>
    <circle cx="22" cy="22" r="19.5" fill="none" stroke="#e01010" stroke-width="3"/>
    <line x1="8" y1="8" x2="36" y2="36" stroke="#e01010" stroke-width="3"/>
  </svg>

  <p class="bill-summary">Lorem ipsum dolor sit amet, consectetur adipiscing elit. Nam condimentum leo sed nisi malesuada, sed accumsan metus ultricies. Donec eleifend nibh in ultrices tempus. Morbi id tempor lorem. Suspendisse potenti. Fusce at augue pulvinar, ultricies nisl id, bibendum est. Cras semper ac nulla ut vulputate. Nam faucibus sagittis odio, quis molestie elit sollicitudin et. Nam dapibus fringilla orci, quis efficitur leo consectetur eu. Vivamus dui lectus, mollis a condimentum consequat, ullamcorper porta lectus. Vivamus sit amet justo enim. Donec nec lorem mi. Lorem ipsum dolor sit amet, consectetur adipiscing elit. Nam condimentum leo sed nisi malesuada, sed accumsan metus ultricies. Donec eleifend nibh in ultrices tempus. Morbi id tempor lorem. Suspendisse potenti. Fusce at augue pulvinar, ultricies nisl id, bibendum est. Cras semper ac nulla ut vulputate. Nam faucibus sagittis odio, quis molestie elit sollicitudin et. Nam dapibus fringilla orci, quis efficitur leo consectetur eu. Vivamus dui lectus, mollis a condimentum consequat, ullamcorper porta lectus. Vivamus sit amet justo enim. Donec nec lorem mi. Lorem ipsum dolor sit amet, consectetur adipiscing elit. Nam condimentum leo sed nisi malesuada, sed accumsan metus ultricies. Donec eleifend nibh in ultrices tempus. Morbi id tempor lorem.</p>

  <div class="vote-options">
    <div class="vote no">
      <div class="button"><svg width="26" height="26" viewBox="0 0 26 26" aria-hidden="true"><path d="M3 3 L23 23 M23 3 L3 23" stroke="#fff" stroke-width="3.5" stroke-linecap="round"/></svg></div>
      <span class="label">No</span>
    </div>
    <div class="vote party">
      <div class="button"><svg width="34" height="34" viewBox="0 0 34 34" aria-hidden="true">
        <path d="M6 9 H28 L17 20 Z" fill="none" stroke="#fff" stroke-width="2" stroke-linejoin="round"/>
        <path d="M10 13 H24" stroke="#fff" stroke-width="2"/>
        <path d="M17 20 V29 M12 29 H22" stroke="#fff" stroke-width="2" stroke-linecap="round"/>
        <path d="M20 9 L24 4" stroke="#fff" stroke-width="2" stroke-linecap="round"/>
      </svg></div>
      <span class="label">Party</span>
    </div>
    <div class="vote yes">
      <div class="button"><svg width="30" height="24" viewBox="0 0 30 24" aria-hidden="true"><path d="M3 12 L11 20 L27 4" fill="none" stroke="#fff" stroke-width="3.5" stroke-linecap="round" stroke-linejoin="round"/></svg></div>
      <span class="label">Yes</span>
    </div>
  </div>

  <div class="chamber"><span class="dot"></span>Legislative Council</div>
  <div class="bill-counter">1 / 77</div>

  <nav class="nav-bar">
    <div class="nav-item" aria-label="Settings">
      <svg width="44" height="44" viewBox="0 0 44 44" aria-hidden="true">
        <g fill="#fff">
          <circle cx="22" cy="22" r="14"/>
          <rect x="18" y="2" width="8" height="9" rx="1"/>
          <rect x="18" y="2" width="8" height="9" rx="1" transform="rotate(45 22 22)"/>
          <rect x="18" y="2" width="8" height="9" rx="1" transform="rotate(90 22 22)"/>
          <rect x="18" y="2" width="8" height="9" rx="1" transform="rotate(135 22 22)"/>
          <rect x="18" y="2" width="8" height="9" rx="1" transform="rotate(180 22 22)"/>
          <rect x="18" y="2" width="8" height="9" rx="1" transform="rotate(225 22 22)"/>
          <rect x="18" y="2" width="8" height="9" rx="1" transform="rotate(270 22 22)"/>
          <rect x="18" y="2" width="8" height="9" rx="1" transform="rotate(315 22 22)"/>
        </g>
        <circle cx="22" cy="22" r="6.5" fill="var(--nav-bar)"/>
      </svg>
    </div>
    <div class="nav-item" aria-label="Help">
      <svg width="44" height="44" viewBox="0 0 44 44" aria-hidden="true">
        <circle cx="22" cy="22" r="21" fill="#fff"/>
        <path d="M15.5 17 A6.5 6.5 0 1 1 24.5 23 C22.5 24 22 25 22 28" fill="none" stroke="var(--nav-bar)" stroke-width="4.5" stroke-linecap="round"/>
        <circle cx="22" cy="34" r="2.8" fill="var(--nav-bar)"/>
      </svg>
    </div>
  </nav>
</body>
</html>
```